Aid, Development & Consulting Firm

Brantwell Fennimore Consulting Pty Ltd is a small firm in Australia whose principal works in the area of aid and development. His experience is broad ranging from aid project design and evaluation; to offering security advice in running aid operations in dangerous situations. He works with governments and private firms in conducting training for personnel travelling to work in dangerous or difficult regions. He has worked for many years with NGO's (aid organisations) and consults to the WCA. He works in locations all over the globe which include trouble spots like Iraq and Sudan, to sleepier locales like Samoa and Fiji. Being on Asia's doorstep much time is spent in Asia eg Indonesia, Vietnam. He is often called on to monitor and evaluate aid projects throughtout the globe.

Target Market(s)

Government Aid Divisions eg in Oz, PacRelief; WCA; NGO's and consulting firms who work in developing countries

Industry/Entity Type

Security

Requirements
Nice to have
• Try and incorporate a global feel without being obvious i.e. no starving children as the primary work done is a step beyond obvious aid relief. Something very simple but bold and stylish as card holder is not a "touchy" feely person
Should not have
• No starving kid type scenarios. Prefer no pictures

```html
<!DOCTYPE html>
<html lang="en">
<head>
<meta charset="utf-8">
<title>Brantwell Fennimore Consulting – Business Card</title>
<link rel="stylesheet" href="https://fonts.googleapis.com/css2?family=Archivo+Narrow:wght@500&family=Arimo:wght@400;700&family=Michroma&display=swap">
<style>
  :root {
    --backdrop: #ebebec;
    --front-bg: #000000;
    --back-bg: #87888c;
    --accent: #1e9bd7;
    --icon-blue: #1c5b9e;
    --text-light: #ffffff;
    --halo-front: rgba(110, 110, 110, 0.55);
    --halo-back: rgba(100, 100, 102, 0.55);
  }
  * { margin: 0; padding: 0; box-sizing: border-box; }
  html, body { width: 1200px; height: 900px; overflow: hidden; }
  body { background: var(--backdrop); position: relative; font-family: "Arimo", Arial, sans-serif; }

  .card {
    position: absolute;
    left: 281px;
    width: 637px;
    height: 389px;
    overflow: hidden;
    box-shadow: 4px 4px 6px rgba(0,0,0,0.25);
  }
  .card--front { top: 41px; background: var(--front-bg); }
  .card--back  { top: 459px; background: var(--back-bg); }

  .halo {
    position: absolute;
    border-radius: 50%;
    width: 300px;
    height: 300px;
  }
  .card--front .halo { left: 352px; top: 120px; background: var(--halo-front); }
  .card--back  .halo { left: 352px; top: 130px; background: var(--halo-back); }

  .brand-dot {
    position: absolute;
    left: 268px;
    top: 6px;
    width: 100px;
    height: 100px;
    border-radius: 50%;
    background: var(--accent);
  }
  .company-name {
    position: absolute;
    top: 118px;
    left: 0; right: 0;
    text-align: center;
    font-family: "Archivo Narrow", "Arial Narrow", sans-serif;
    font-weight: 500;
    font-size: 33px;
    color: var(--text-light);
    letter-spacing: 0.2px;
  }
  .tagline {
    position: absolute;
    top: 165px;
    left: 0; right: 0;
    text-align: center;
    font-family: "Michroma", sans-serif;
    font-size: 13px;
    letter-spacing: 2.5px;
    color: var(--accent);
  }
  .tagline .sep { margin: 0 24px; }
  .holder-name {
    position: absolute;
    top: 240px;
    left: 0; right: 0;
    text-align: center;
    font-weight: 700;
    font-size: 23px;
    letter-spacing: 0.5px;
    color: var(--text-light);
  }
  .holder-role {
    position: absolute;
    top: 269px;
    left: 0; right: 0;
    text-align: center;
    font-family: "Michroma", sans-serif;
    font-size: 15px;
    letter-spacing: 2px;
    color: var(--accent);
    font-variant: small-caps;
  }

  .contact {
    position: absolute;
    left: 52px;
    color: var(--text-light);
    font-size: 18px;
    line-height: 27.5px;
  }
  .contact--address { top: 127px; }
  .contact--lines { top: 237px; }
  .contact li { list-style: none; display: flex; align-items: center; }
  .contact svg { width: 24px; height: 22px; margin-right: 17px; fill: var(--icon-blue); flex: none; }
  .contact .spacer { width: 24px; margin-right: 17px; flex: none; }
</style>
</head>
<body>

<section class="card card--front">
  <div class="halo" aria-hidden="true"></div>
  <div class="brand-dot" aria-hidden="true"></div>
  <h1 class="company-name">Brantwell Fennimore Consulting Pty Ltd</h1>
  <p class="tagline">AID<span class="sep">|</span>DEVELOPMENT<span class="sep">|</span>CONSULTING</p>
  <p class="holder-name">B. Brantwell Fennimore</p>
  <p class="holder-role">Director</p>
</section>

<section class="card card--back">
  <div class="halo" aria-hidden="true"></div>
  <ul class="contact contact--address">
    <li><svg viewBox="0 0 24 22" aria-hidden="true"><path d="M12 0a7 7 0 0 0-7 7c0 5 7 15 7 15s7-10 7-15a7 7 0 0 0-7-7z"/></svg>42 Kestrel Street</li>
    <li><span class="spacer"></span>Marden Heights</li>
    <li><span class="spacer"></span>SA 5070 Australia</li>
  </ul>
  <ul class="contact contact--lines">
    <li><svg viewBox="0 0 24 22" aria-hidden="true"><path d="M2 6c0-3 4-4 10-4s10 1 10 4v2h-5V6H7v2H2z"/><path d="M5 10h14l2 10H3z M9 13h6v4H9z" fill-rule="evenodd"/></svg>+61 8 8140 5592</li>
    <li><svg viewBox="0 0 24 22" aria-hidden="true"><path d="M7 0h10a2 2 0 0 1 2 2v18a2 2 0 0 1-2 2H7a2 2 0 0 1-2-2V2a2 2 0 0 1 2-2zm1 3v14h8V3z M12 18.3a1.2 1.2 0 1 0 0 2.4 1.2 1.2 0 0 0 0-2.4z" fill-rule="evenodd"/></svg>+61 (0) 4127 30615</li>
    <li><svg viewBox="0 0 24 22" aria-hidden="true"><path d="M1 4h22v15H1zm2 2v.5l9 6 9-6V6zm0 3v8h18V9l-9 6z" fill-rule="evenodd"/></svg>brantwell@coralnet.com</li>
    <li><svg viewBox="0 0 24 22" aria-hidden="true"><path d="M1 4h22v15H1zm2 2v.5l9 6 9-6V6zm0 3v8h18V9l-9 6z" fill-rule="evenodd"/></svg>fennimoreb@mailbay.com</li>
  </ul>
</section>

</body>
</html>
```